Veldmark Supplies Business Card

Professional business card that stand out to our potential customers. Front and back with clean modern design

Industry/Entity Type

Oil and gas

Contact Information for Business Card

Name, address, website , office phone and cell number

Requirements
Must have
• Editable files for each employee

```html
<!DOCTYPE html>
<html lang="en">
<head>
<meta charset="utf-8">
<title>Veldmark Supplies Business Card</title>
<link href="https://fonts.googleapis.com/css2?family=Montserrat:wght@400;500;700;800&display=swap" rel="stylesheet">
<style>
  :root {
    --red: #e82127;
    --blue: #14b0d4;
    --green: #129a48;
    --ink: #231f20;
    --text: #2b2b2b;
    --paper: #ffffff;
    --stage: #3a3a3a;
  }
  * { box-sizing: border-box; margin: 0; padding: 0; }
  html, body {
    width: 1200px; height: 988px; overflow: hidden;
    background: var(--stage);
    font-family: "Montserrat", sans-serif;
  }
  .canvas {
    position: relative; width: 1200px; height: 988px;
    display: flex; flex-direction: column; align-items: center;
    justify-content: center; gap: 40px;
  }
  .card {
    position: relative; width: 760px; height: 434px;
    border-radius: 26px; overflow: hidden;
  }
  /* Back */
  .card-back {
    background: var(--ink);
    display: flex; align-items: center; justify-content: center; gap: 22px;
  }
  .card-back .brand-dot {
    width: 46px; height: 46px; border-radius: 50%; background: var(--red);
  }
  .card-back .brand-name {
    font-weight: 800; font-size: 46px; letter-spacing: 1px;
    text-transform: uppercase; color: var(--blue);
  }
  /* Front */
  .card-front { background: var(--paper); }
  .front-brand {
    position: absolute; left: 52px; top: 52px;
    display: flex; align-items: center; gap: 12px;
  }
  .front-brand .brand-square { width: 22px; height: 22px; background: var(--red); }
  .front-brand .brand-name {
    font-weight: 800; font-size: 24px; text-transform: uppercase;
    letter-spacing: 1px; color: var(--red);
  }
  .brand-feature {
    position: absolute; right: 56px; top: 70px; width: 290px; height: 294px;
    display: flex; align-items: center; justify-content: center; text-align: center;
    font-weight: 800; font-size: 50px; line-height: 1.05; text-transform: uppercase;
    color: var(--red);
  }
  .accent-tab {
    position: absolute; left: 0; top: 170px; width: 18px; height: 62px;
    background: var(--red); border-radius: 0 8px 8px 0;
  }
  .person { position: absolute; left: 52px; top: 162px; }
  .person-name { font-weight: 800; font-size: 38px; line-height: 1; }
  .person-name .first { color: var(--red); }
  .person-name .last { color: var(--green); }
  .person-title { margin-top: 8px; font-size: 16px; font-weight: 500; color: var(--text); }
  .divider { position: absolute; left: 52px; top: 262px; width: 22px; height: 2px; background: var(--red); }
  .contacts {
    position: absolute; left: 52px; top: 282px; list-style: none;
    font-size: 15px; color: var(--text);
  }
  .contacts li { display: flex; align-items: center; gap: 12px; height: 24px; }
  .contacts svg { width: 14px; height: 14px; flex: none; }
</style>
</head>
<body>
<main class="canvas">
  <section class="card card-back" aria-label="Card back">
    <span class="brand-dot"></span>
    <span class="brand-name">Veldmark Supplies</span>
  </section>

  <section class="card card-front" aria-label="Card front">
    <div class="front-brand">
      <span class="brand-square"></span>
      <span class="brand-name">Veldmark Supplies</span>
    </div>
    <div class="brand-feature">Veldmark<br>Supplies</div>
    <span class="accent-tab"></span>
    <div class="person">
      <h1 class="person-name"><span class="first">Daniel</span> <span class="last">Harlow</span></h1>
      <p class="person-title">Manager</p>
    </div>
    <span class="divider"></span>
    <ul class="contacts">
      <li><svg viewBox="0 0 16 16"><path fill="var(--red)" d="M3 1l3 3-2 2a9 9 0 0 0 6 6l2-2 3 3-2 2C7 15 1 9 1 3z"/></svg>1-555-014-0277</li>
      <li><svg viewBox="0 0 16 16"><path fill="var(--green)" d="M1 3h14v10H1z"/><path fill="none" stroke="#fff" stroke-width="1.4" d="M1 3l7 6 7-6"/></svg>dharlow@kestrelparts.vn</li>
      <li><svg viewBox="0 0 16 16" fill="none" stroke="var(--red)" stroke-width="1.4"><circle cx="8" cy="8" r="6.5"/><ellipse cx="8" cy="8" rx="3" ry="6.5"/><path d="M1.5 8h13"/></svg>www.kestrelparts.vn</li>
      <li><svg viewBox="0 0 16 16" fill="none" stroke="var(--green)" stroke-width="1.4"><circle cx="8" cy="8" r="6.5"/><ellipse cx="8" cy="8" rx="3" ry="6.5"/><path d="M1.5 8h13"/></svg>www.kestrelparts.com</li>
      <li><svg viewBox="0 0 16 16"><path fill="var(--red)" d="M8 1a5 5 0 0 0-5 5c0 4 5 9 5 9s5-5 5-9a5 5 0 0 0-5-5zm0 3a2 2 0 1 1 0 4 2 2 0 0 1 0-4z"/></svg>Da Nang, Vietnam</li>
    </ul>
  </section>
</main>
</body>
</html>
```